Redesign Website - Current one too plain

The description is in the uploaded file. Please let me know if you need any more information. I'd prefer it if someone could implement the design to a WordPress site but the best design will win, regardless.
I would like the forms to look nice as well
UPDATE:
I don't think we can use the images that I provided, I think they make the site look a bit 'cheap' and I really don't know how to replace them. One thought I have had is to make the "Simple, Unique, Effective" a second feature on the right side of the page with the search on the left
Target Market(s)
Small companies, private sellers of cars and people who rent their caravan/holiday home out
Industry/Entity Type
Advertising
Number of Pages Required
3 page
Colors
Designer to choose colors to be used in the design.
Look and feel
Each slider illustrates characteristics of the customer's brand and the style your logo design should communicate.

```html
<!DOCTYPE html>
<html lang="en">
<head>
<meta charset="utf-8">
<title>Codora – Find a business by its code</title>
<link href="https://fonts.googleapis.com/css2?family=Mulish:wght@300;400;700;800;900&display=swap" rel="stylesheet">
<style>
:root{
  --lime:#dcf400;
  --ink:#0c0c0c;
  --paper:#f7f7f7;
  --plate-dark:#555555;
  --plate-mid:#666666;
  --grey-line:#d9d9d9;
  --footer:#f3f3f3;
  --text:#222222;
}
*{box-sizing:border-box;margin:0;padding:0}
html,body{width:1200px;height:2280px;overflow:hidden}
body{font-family:"Mulish",sans-serif;color:var(--text);background:#fff;position:relative;font-weight:300}
.abs{position:absolute}

.dark-band{left:0;top:0;width:1200px;height:1273px;
  background:linear-gradient(160deg,#2a2a2a 0%,#121212 40%,#1d1d1d 60%,#050505 100%)}
.hero-panel{left:-8px;top:-8px;width:1216px;height:728px;
  background:linear-gradient(135deg,#f2f2f2 0%,#fafafa 50%,#ececec 100%);
  border:8px solid var(--lime);border-top:none;
  border-radius:0 0 430px 380px / 0 0 340px 290px}

.brand{display:flex;align-items:center;gap:14px;font-weight:300;color:var(--ink)}
.brand-dot{width:54px;height:54px;border-radius:50%;background:var(--ink)}
.site-brand{left:113px;top:25px;font-size:31px}
.site-nav{left:625px;top:54px}
.site-nav a{color:var(--ink);text-decoration:none;font-size:18px;font-weight:300;position:absolute;white-space:nowrap}

.plate{left:136px;top:206px;width:352px;height:257px;border-radius:14px;overflow:hidden;background:#fff;box-shadow:0 3px 8px rgba(0,0,0,.15)}
.plate-band{position:absolute;left:0;width:352px;height:57px;display:flex}
.plate-band div{flex:1;display:flex;align-items:center;justify-content:center}
.plate-band .l{background:var(--plate-mid)}
.plate-band .r{background:var(--plate-dark)}
.plate-band.bottom .l{background:var(--plate-dark)}
.plate-band.bottom .r{background:var(--plate-mid)}
.plate-band.top{top:0}
.plate-band.bottom{bottom:0}
.plate-chars{position:absolute;top:57px;left:0;width:352px;height:143px;display:flex;font-weight:900;font-size:140px;line-height:143px;color:#000}
.plate-chars span{flex:1;text-align:center}

.pill{height:37px;border-radius:19px;background:var(--ink);color:var(--lime);font-size:18px;font-weight:400;display:flex;align-items:center;justify-content:center}
.btn-lime{background:var(--lime);color:var(--ink);font-weight:300;display:flex;align-items:center;justify-content:center}
.search-btn{left:252px;top:572px;width:108px;height:42px;border-radius:21px;font-size:18px;box-shadow:3px 3px 0 #111}

.vehicles{left:575px;top:195px;width:600px;height:440px;border-radius:40px;
  background:radial-gradient(ellipse at 55% 55%,#a9a7a2 0%,#c9c7c3 45%,rgba(235,235,235,0) 75%)}

.feature{width:283px;height:232px;top:862px;background:var(--paper);border-radius:140px 140px 115px 115px;text-align:center}
.feature-icon{width:137px;height:137px;border-radius:50%;background:var(--paper);position:absolute;left:73px;top:-27px;display:flex;align-items:center;justify-content:center}
.feature-icon i{display:block;width:68px;height:68px;border-radius:50%;background:radial-gradient(circle,#5aa7e6 0%,#e4b48c 55%,#2a2a2a 100%)}
.feature h3{position:absolute;top:114px;width:100%;font-size:20px;font-weight:800;color:var(--ink)}
.feature p{position:absolute;top:149px;left:34px;right:34px;font-size:16px;line-height:24px;color:var(--ink)}
.advertise-btn{left:477px;top:1155px;width:246px;height:43px;border-radius:22px;font-size:18px}

.section-title{left:0;top:1362px;width:1200px;text-align:center;font-size:30px;font-weight:800;color:var(--ink)}
.review{top:1447px;width:305px;height:284px;border:1.5px solid #555;border-radius:6px;background:#fff}
.review-head{height:100px;border-bottom:1px solid var(--grey-line);position:relative}
.avatar{position:absolute;left:20px;top:17px;width:66px;height:66px;border-radius:50%;background:linear-gradient(160deg,#c9c0b6,#7d6e62)}
.review-name{position:absolute;left:101px;top:28px;font-size:18px;font-weight:800;color:var(--ink)}
.review-role{position:absolute;left:101px;top:52px;font-size:16px}
.review-body{position:absolute;left:20px;right:20px;top:117px;font-size:15.5px;line-height:22.3px;text-align:justify}
.stars{position:absolute;left:20px;top:238px;display:flex}
.view-more{left:534px;top:1777px;width:133px;height:43px;border-radius:22px;background:var(--ink);color:#fff;font-size:18px;font-weight:300;display:flex;align-items:center;justify-content:center}

.site-footer{left:0;top:1911px;width:1200px;height:369px;background:var(--footer);border-radius:70px 70px 0 0}
.footer-brand{left:113px;top:1995px;font-size:38px}
.footer-brand .brand-dot{width:72px;height:72px}
.footer-col{top:1998px}
.footer-col h4{font-size:16px;font-weight:800;color:var(--ink);padding-bottom:10px;border-bottom:1.5px solid var(--lime);width:115px;margin-bottom:14px}
.footer-col li{list-style:none;font-size:16px;line-height:29px;color:var(--ink)}
.help li{line-height:24px}
.contact-list li{display:flex;gap:9px;line-height:26px}
.contact-list svg{flex:none;margin-top:6px}
.footer-rule{left:0;top:2218px;width:1200px;height:1px;background:var(--lime)}
.copyright{left:0;top:2244px;width:1200px;text-align:center;font-size:13.5px;color:var(--ink)}
</style>
</head>
<body>

<div class="abs dark-band"></div>
<div class="abs hero-panel"></div>

<header>
  <div class="abs brand site-brand"><span class="brand-dot"></span>Codora</div>
  <nav class="abs site-nav">
    <a style="left:0;top:0">Home</a>
    <a style="left:92px;top:0">Advertise</a>
    <a style="left:209px;top:0">Contact</a>
    <a style="left:315px;top:0">Register</a>
    <a style="left:423px;top:0">Login</a>
  </nav>
</header>

<section class="hero">
  <div class="abs plate">
    <div class="plate-band top">
      <div class="l"><svg width="34" height="20" viewBox="0 0 34 20"><path d="M3 17 17 4 31 17" fill="none" stroke="var(--lime)" stroke-width="4"/></svg></div>
      <div class="r"><svg width="34" height="20" viewBox="0 0 34 20"><path d="M3 17 17 4 31 17" fill="none" stroke="var(--lime)" stroke-width="4"/></svg></div>
    </div>
    <div class="plate-chars"><span>A</span><span>1</span></div>
    <div class="plate-band bottom">
      <div class="l"><svg width="34" height="20" viewBox="0 0 34 20"><path d="M3 3 17 16 31 3" fill="none" stroke="var(--lime)" stroke-width="4"/></svg></div>
      <div class="r"><svg width="34" height="20" viewBox="0 0 34 20"><path d="M3 3 17 16 31 3" fill="none" stroke="var(--lime)" stroke-width="4"/></svg></div>
    </div>
  </div>
  <div class="abs pill" style="left:139px;top:500px;width:88px">Car</div>
  <div class="abs pill" style="left:252px;top:500px;width:104px">Caravan</div>
  <div class="abs pill" style="left:381px;top:500px;width:107px">Company</div>
  <div class="abs btn-lime search-btn">Search</div>
  <div class="abs vehicles" role="img" aria-label="Photo of a caravan, a van and a silver car, each tagged with a short code"></div>
</section>

<section class="features">
  <div class="abs feature" style="left:114px">
    <div class="feature-icon"><i role="img" aria-label="Icon of a finger touching a light bulb"></i></div>
    <h3>Simple</h3>
    <p>create &nbsp;your advert and display your code</p>
  </div>
  <div class="abs feature" style="left:459px">
    <div class="feature-icon"><i role="img" aria-label="Icon of a fingerprint under a magnifier"></i></div>
    <h3>Unique</h3>
    <p>customers find you by an easy-to-remember code</p>
  </div>
  <div class="abs feature" style="left:804px">
    <div class="feature-icon"><i role="img" aria-label="Icon of a target with a tick"></i></div>
    <h3>Effective</h3>
    <p>customers are directed to you and not a list of your competitors</p>
  </div>
  <div class="abs btn-lime advertise-btn">Advertise Your Company</div>
</section>

<svg width="0" height="0" style="position:absolute"><defs><polygon id="st" points="8,0 10.4,5.4 16,6 11.8,9.8 13,15.6 8,12.6 3,15.6 4.2,9.8 0,6 5.6,5.4"/></defs></svg>

<section class="testimonials">
  <h2 class="abs section-title">Testimonials</h2>

  <article class="abs review" style="left:113px">
    <div class="review-head">
      <div class="avatar" role="img" aria-label="Portrait photo of the customer"></div>
      <div class="review-name">Sam Porter</div>
      <div class="review-role">Patient</div>
    </div>
    <p class="review-body">Lorem ipsum dolor sit amet, consectetur adipiscing elit, sed do eiusmod tempor incididunt ut labore et dolore magna aliqua. Quis ipsum suspendisse ultrices gravida.</p>
    <div class="stars"><svg width="82" height="16" viewBox="0 0 82 16" fill="var(--lime)"><use href="#st"/><use href="#st" x="16.5"/><use href="#st" x="33"/><use href="#st" x="49.5"/><use href="#st" x="66"/></svg></div>
  </article>

  <article class="abs review" style="left:448px">
    <div class="review-head">
      <div class="avatar" role="img" aria-label="Portrait photo of the customer"></div>
      <div class="review-name">Sam Porter</div>
      <div class="review-role">Patient</div>
    </div>
    <p class="review-body">Lorem ipsum dolor sit amet, consectetur adipiscing elit, sed do eiusmod tempor incididunt ut labore et dolore magna aliqua. Quis ipsum suspendisse ultrices gravida.</p>
    <div class="stars"><svg width="82" height="16" viewBox="0 0 82 16" fill="var(--lime)"><use href="#st"/><use href="#st" x="16.5"/><use href="#st" x="33"/><use href="#st" x="49.5"/><use href="#st" x="66"/></svg></div>
  </article>

  <article class="abs review" style="left:783px">
    <div class="review-head">
      <div class="avatar" role="img" aria-label="Portrait photo of the customer"></div>
      <div class="review-name">Sam Porter</div>
      <div class="review-role">Patient</div>
    </div>
    <p class="review-body">Lorem ipsum dolor sit amet, consectetur adipiscing elit, sed do eiusmod tempor incididunt ut labore et dolore magna aliqua. Quis ipsum suspendisse ultrices gravida.</p>
    <div class="stars"><svg width="82" height="16" viewBox="0 0 82 16" fill="var(--lime)"><use href="#st"/><use href="#st" x="16.5"/><use href="#st" x="33"/><use href="#st" x="49.5"/><use href="#st" x="66"/></svg></div>
  </article>

  <div class="abs view-more">View More</div>
</section>

<footer>
  <div class="abs site-footer"></div>
  <div class="abs brand footer-brand"><span class="brand-dot"></span>Codora</div>

  <div class="abs footer-col" style="left:357px">
    <h4>Contact</h4>
    <ul class="contact-list">
      <li><svg width="12" height="15" viewBox="0 0 12 15"><path d="M6 0a6 6 0 0 0-6 6c0 4.5 6 9 6 9s6-4.5 6-9a6 6 0 0 0-6-6zm0 8.3A2.3 2.3 0 1 1 6 3.7a2.3 2.3 0 0 1 0 4.6z" fill="#111"/></svg><span>#12, Elm Road,<br>Townsville - 302114</span></li>
      <li><svg width="14" height="14" viewBox="0 0 14 14"><path d="M3 0l2.5 3.5-1.6 1.7a8 8 0 0 0 4.9 4.9l1.7-1.6L14 11l-1.5 2.5C6 13.5.5 8 .5 1.5z" fill="#111"/></svg><span>(+1) 555 010 2040</span></li>
      <li><svg width="14" height="11" viewBox="0 0 14 11"><rect width="14" height="11" rx="1" fill="#111"/><path d="M1 1.5 7 6l6-4.5" fill="none" stroke="#f3f3f3" stroke-width="1.3"/></svg><span>info@codora.com</span></li>
    </ul>
  </div>

  <div class="abs footer-col" style="left:612px">
    <h4>Quick Links</h4>
    <ul><li>Home</li><li>Advertise</li><li>Contact</li><li>Register</li><li>Login</li></ul>
  </div>

  <div class="abs footer-col help" style="left:785px">
    <h4>Help Links</h4>
    <ul><li>Care</li><li>Privacy Policy</li><li>FAQ</li><li>Terms &amp; Conditions</li></ul>
  </div>

  <div class="abs footer-col help" style="left:971px">
    <h4>Useful Links</h4>
    <ul><li>Privacy Policy</li><li>Returns</li><li>Contact Us</li></ul>
  </div>

  <div class="abs footer-rule"></div>
  <p class="abs copyright">Copyright © 2023 Codora | All Rights Reserved</p>
</footer>

</body>
</html>
```